Business Card Design - ChoiceCraft

Looking for creative, modern design, two sided for ChoiceCraft that is consistent with color and feel of website www.choicecraftpro.net.
Updates

Back of card will be used to promote products or have a quote revolving around decisions, change, leadership, innovation, creativity. Back should also have space to promote website, but optional to use the icon. Front of the card will need to use the icon and have standard place for name, job title, phone and email. We are not looking to put a mailing address or fax. Also want space to place a few words/phrase explaining what we do...such as individual growth and organizational development or tools, training, information...in addition, want the facebook icon small on the front somewhere as we are also on facebook.

Vector file uploaded of icon.

Target Market(s)

Professional coaching for individual growth and organizational development

Industry/Entity Type

Business

Requirements
Must have
• Icon...see attached.

```html
<!DOCTYPE html>
<html lang="en">
<head>
<meta charset="utf-8">
<title>ChoiceCraft Business Card</title>
<link href="https://fonts.googleapis.com/css2?family=Jost:wght@400;500;600&family=Arimo:wght@400;700&display=swap" rel="stylesheet">
<style>
  :root {
    --stage: #2a2c30;
    --blue-deep: #0a6fc0;
    --blue-mid: #1a8fd8;
    --blue-light: #35bdf0;
    --blue-glow: #5cc6f2;
    --paper: #ffffff;
    --ink: #1d1d1f;
    --ink-soft: #333333;
    --icon: #555555;
    --rule: #b7c6d6;
  }
  * { box-sizing: border-box; margin: 0; padding: 0; }
  html, body { width: 1200px; height: 763px; overflow: hidden; }
  body {
    background: var(--stage);
    display: flex;
    align-items: center;
    justify-content: center;
    gap: 40px;
  }
  .card {
    width: 540px;
    height: 304px;
    position: relative;
    overflow: hidden;
    box-shadow: 0 10px 30px rgba(0,0,0,0.45);
  }

  /* Front */
  .card-front {
    background: var(--paper);
    font-family: "Jost", "Futura", sans-serif;
    color: var(--ink);
  }
  .front-header {
    height: 50px;
    background: linear-gradient(90deg, var(--blue-mid), var(--blue-light));
    display: flex;
    align-items: center;
    justify-content: center;
    color: var(--paper);
    border-bottom: 3px solid var(--paper);
    box-shadow: 0 3px 0 var(--rule);
  }
  .holder-name { font-size: 22px; font-weight: 600; }
  .holder-title { font-size: 17px; font-weight: 400; margin-left: 6px; }
  .brand {
    display: flex;
    align-items: center;
    justify-content: center;
    gap: 18px;
    margin-top: 34px;
  }
  .brand-mark {
    width: 78px; height: 78px;
    border-radius: 50%;
    background: var(--blue-mid);
  }
  .brand-name { font-size: 30px; font-weight: 400; color: var(--ink); }
  .contacts {
    margin-top: 20px;
    font-size: 14px;
    text-align: center;
    line-height: 1.6;
    color: var(--ink-soft);
  }
  .contact-row { display: flex; justify-content: center; gap: 18px; align-items: center; }
  .contact-item { display: inline-flex; align-items: center; gap: 5px; }
  .contact-item svg { width: 12px; height: 12px; fill: var(--icon); }
  .social-square { width: 11px; height: 11px; background: var(--blue-deep); display: inline-block; }
  .front-footer {
    position: absolute;
    left: 0; right: 0; bottom: 0;
    height: 40px;
    background: linear-gradient(90deg, var(--blue-mid), var(--blue-light));
    border-top: 3px solid var(--paper);
    box-shadow: 0 -3px 0 var(--rule);
    color: var(--paper);
    font-size: 15px;
    display: flex;
    align-items: center;
    justify-content: center;
  }

  /* Back */
  .card-back {
    background: radial-gradient(ellipse at 50% 50%, var(--blue-glow) 0%, var(--blue-mid) 45%, var(--blue-deep) 100%);
    font-family: "Arimo", "Arial", sans-serif;
    color: var(--paper);
    display: flex;
    flex-direction: column;
    justify-content: center;
    align-items: center;
    gap: 7px;
    text-align: center;
    padding: 0 24px;
  }
  .quote-text { font-size: 13.5px; line-height: 1.2; }
  .quote-mark { font-family: Georgia, serif; font-weight: 700; font-size: 20px; line-height: 0; vertical-align: -6px; }
  .quote-author { font-size: 13.5px; font-weight: 700; line-height: 1.2; }
</style>
</head>
<body>
  <section class="card card-front">
    <header class="front-header">
      <span class="holder-name">Your Name,</span><span class="holder-title">Title</span>
    </header>
    <div class="brand">
      <span class="brand-mark"></span>
      <span class="brand-name">ChoiceCraft</span>
    </div>
    <div class="contacts">
      <div class="contact-row">
        <span class="contact-item">
          <svg viewBox="0 0 24 24" aria-hidden="true"><path d="M6.6 10.8a15.1 15.1 0 0 0 6.6 6.6l2.2-2.2a1 1 0 0 1 1-.25 11.4 11.4 0 0 0 3.6.57 1 1 0 0 1 1 1V20a1 1 0 0 1-1 1A17 17 0 0 1 3 4a1 1 0 0 1 1-1h3.5a1 1 0 0 1 1 1c0 1.25.2 2.45.57 3.57a1 1 0 0 1-.25 1z"/></svg>
          555-318-240
        </span>
        <span class="contact-item">
          <svg viewBox="0 0 24 24" aria-hidden="true"><path d="M2 5h20v14H2zm2 2v.5l8 5 8-5V7l-8 5z"/></svg>
          info@choicecraftmail.net
        </span>
      </div>
      <div class="contact-row">
        <span class="contact-item">
          <svg viewBox="0 0 24 24" aria-hidden="true"><circle cx="12" cy="12" r="10"/></svg>
          www.choicecraftpro.net
        </span>
        <span class="contact-item">
          <span class="social-square"></span>
          /choicecraftpro
        </span>
      </div>
    </div>
    <footer class="front-footer">Supporting individual growth &amp; organizational development.</footer>
  </section>

  <section class="card card-back">
    <div class="quote">
      <p class="quote-text"><span class="quote-mark">&ldquo;</span>Try not to become a man of success, but rather a man of value.<span class="quote-mark">&rdquo;</span></p>
      <p class="quote-author">- Arthur Wendell</p>
    </div>
    <div class="quote">
      <p class="quote-text"><span class="quote-mark">&ldquo;</span>The only constant is change.<span class="quote-mark">&rdquo;</span></p>
      <p class="quote-author">- Corvin Ashby</p>
    </div>
    <div class="quote">
      <p class="quote-text"><span class="quote-mark">&ldquo;</span>We are what we repeatedly do. Excellence is not an act, it is a habit.<span class="quote-mark">&rdquo;</span></p>
      <p class="quote-author">- Marcus Halden</p>
    </div>
    <div class="quote">
      <p class="quote-text"><span class="quote-mark">&ldquo;</span>Simplicity is the ultimate sophistication.<span class="quote-mark">&rdquo;</span></p>
      <p class="quote-author">- Lorenzo Varesi</p>
    </div>
    <div class="quote">
      <p class="quote-text"><span class="quote-mark">&ldquo;</span>Life is not fair - get used to it.<span class="quote-mark">&rdquo;</span></p>
      <p class="quote-author">- Bruce Galloway</p>
    </div>
  </section>
</body>
</html>
```